Corvina Dental personal information forms

We are a Dental Practice that require an update to our information forms, there are 3 versions of it.
I will attach our old ones, we need to keep the same information on there, we just want them to look better and use our current logo and colours.
Our website is www.corvinadental.net
Our facebook is www.friendspage.net/corvinadentalbelmorewalk/
..................................................................................................

Target Market(s)

Everyone, easy to read

Industry/Entity Type

Dental Clinic

Colors
0692cd
34a6d7
cee9f5
ffffff
0255a3
3276b5

Requirements
Must have
• Logo
• Our colours
• same information as the uploaded versions
Should not have
• any other colour besides the blues, black and white

```html
<!DOCTYPE html>
<html lang="en">
<head>
<meta charset="utf-8">
<title>Corvina Dental – Medical History Update</title>
<link href="https://fonts.googleapis.com/css2?family=Montserrat:wght@400;500;600;700&display=swap" rel="stylesheet">
<style>
  :root{
    --blue-deep:#0255a3;
    --blue:#0692cd;
    --blue-mid:#3276b5;
    --blue-light:#34a6d7;
    --blue-pale:#cee9f5;
    --white:#ffffff;
    --ink:#111111;
    --rule:#d8dde2;
    --field:#e9ecef;
  }
  *{box-sizing:border-box;margin:0;padding:0}
  html,body{width:781px;height:1200px;overflow:hidden;background:var(--white)}
  body{font-family:"Montserrat",sans-serif;color:var(--ink);position:relative}
  .page{position:absolute;inset:0;background:var(--white)}
  .abs{position:absolute}

  .header-band,.footer-band{position:absolute;left:0;width:781px}
  .header-band{top:0;height:150px}
  .footer-band{bottom:0;height:80px}

  .brand{left:60px;top:44px;display:flex;align-items:center;gap:12px;color:var(--white)}
  .brand-mark{width:14px;height:14px;border-radius:50%;background:var(--white)}
  .brand-name{font-weight:600;font-size:30px;line-height:36px}

  .contact{left:560px;top:24px;color:var(--white)}
  .contact-phone{display:flex;align-items:center;gap:8px;font-weight:700;font-size:24px}
  .contact-web{display:flex;align-items:center;gap:10px;font-size:12.5px;margin-top:10px;padding-left:2px}
  .contact-web span{margin-left:14px}

  .practitioners{left:22px;top:186px;color:var(--blue-deep);font-weight:700;font-size:13px;line-height:20px}
  .sticker-box{left:473px;top:172px;width:286px;height:65px;border:1px solid var(--rule);display:flex;align-items:center;justify-content:center;font-style:italic;font-size:13px;font-weight:500}

  .welcome{left:22px;top:274px;color:var(--blue-mid);font-size:12.5px;font-weight:500}
  .intro{left:22px;top:298px;width:737px;font-size:12.5px;line-height:17.5px}
  .intro b{font-weight:700}

  .question{left:22px;width:737px;border-top:1px solid var(--rule)}
  .question-row{display:flex;justify-content:space-between;padding:6px 12px 0 12px;font-size:11.5px;line-height:16px}
  .question-row .yn{font-weight:700;font-size:12px}
  .answer-field{margin-top:6px;height:24px;background:var(--field)}

  .conditions-title{left:34px;top:559px;font-size:11.5px}
  .condition-list{top:590px;list-style:none;font-size:11.5px;line-height:18.8px}
  .condition-list li{position:relative;padding-left:20px}
  .condition-list li::before{content:"";position:absolute;left:0;top:4px;width:8px;height:9px;border-left:2px solid var(--ink);border-bottom:2px solid var(--ink)}

  .declaration{left:22px;top:1022px;width:740px;font-weight:700;font-size:11px;line-height:15px}
  .signature{left:22px;top:1066px;font-size:10.5px;display:flex;align-items:flex-end;gap:6px}
  .sign-line{display:inline-block;border-bottom:1px solid #888;height:10px}

  .footer-url{left:0;width:781px;top:1160px;text-align:center;color:var(--white);font-size:24px;font-weight:500;letter-spacing:0.3px}
</style>
</head>
<body>
<div class="page">

  <svg class="header-band" viewBox="0 0 781 150" preserveAspectRatio="none" aria-hidden="true">
    <defs>
      <linearGradient id="headGrad" x1="0" y1="0" x2="1" y2="0">
        <stop offset="0" stop-color="#0255a3"/>
        <stop offset="0.5" stop-color="#0692cd"/>
        <stop offset="1" stop-color="#0255a3"/>
      </linearGradient>
    </defs>
    <path d="M0 0H781V122C640 140 520 118 400 128C260 140 130 118 0 132Z" fill="url(#headGrad)"/>
    <path d="M0 132C130 118 260 140 400 128C520 118 640 140 781 122V128C640 146 520 124 400 134C260 146 130 124 0 138Z" fill="#34a6d7" opacity="0.5"/>
  </svg>

  <div class="abs brand">
    <span class="brand-mark" aria-hidden="true"></span>
    <span class="brand-name">Corvina Dental</span>
  </div>

  <div class="abs contact">
    <div class="contact-phone">
      <svg width="22" height="22" viewBox="0 0 22 22" aria-hidden="true">
        <circle cx="11" cy="11" r="9.5" fill="none" stroke="#fff" stroke-width="1.8"/>
        <path d="M7.5 6.5l2 -0.5 1 2.5-1.2 1c.6 1.3 1.4 2.1 2.7 2.7l1-1.2 2.5 1-.5 2c-3.8.2-7.6-3.6-7.5-7.5z" fill="#fff"/>
      </svg>
      08 5550 0147
    </div>
    <div class="contact-web">
      <svg width="10" height="10" viewBox="0 0 10 10" aria-hidden="true"><circle cx="5" cy="5" r="4.5" fill="#fff" opacity="0.85"/></svg>
      <span>www.corvinadental.net</span>
    </div>
  </div>

  <div class="abs practitioners">Dr.Lewis Harrow &amp; Dr. Ethan Marlow<br>Dental Surgeons</div>
  <div class="abs sticker-box">Affix patient sticker here.</div>

  <div class="abs welcome">Welcome back to our practice!</div>
  <p class="abs intro"><b>THIS INFORMATION IS CONFIDENTIAL</b> and is necessary to enable us to offer you <b>THE BEST POSSIBLE</b> CARE.It is now mandatory to have a written updated medical history every 2 years and we would appreciate your time in thoroughly completing this form.</p>

  <div class="abs question" style="top:407px">
    <div class="question-row"><span>Are you currently or have you taken any prescribed medication or dietary supplements in the last 12 months?<br>(If YES please list below)</span><span class="yn">YES/NO</span></div>
    <div class="answer-field"></div>
  </div>
  <div class="abs question" style="top:474px;border-top:none">
    <div class="question-row"><span>Allergies / Reactions?<br>(If YES please list below)</span><span class="yn">YES/NO</span></div>
    <div class="answer-field"></div>
  </div>

  <div class="abs conditions-title">Have you ever had or are you suffering from any of the following? Please tick any that apply :</div>
  <ul class="abs condition-list" style="left:48px">
    <li>Rheumatic fever</li><li>Epilepsy</li><li>Asthma</li><li>Tuberculosis</li><li>Radiation Therapy</li><li>Dizziness, fainting</li><li>Hepatitis A B or C</li><li>Recent eye surgery</li>
  </ul>
  <ul class="abs condition-list" style="left:285px">
    <li>Diabetes</li><li>kidney disease</li><li>Heart attack</li><li>High Blood Pressure</li><li>Bleeding problems</li><li>Artificial joints</li><li>Respiratory Problems</li>
  </ul>
  <ul class="abs condition-list" style="left:524px">
    <li>HIV Positive</li><li>High cholesterol</li><li>Cancer</li><li>Pace-maker</li><li>Osteoporosis</li><li>Heart rate problems</li><li>Heart murmur</li>
  </ul>

  <div class="abs question" style="top:772px;border-top:none">
    <div class="question-row"><span>Do you have any disease,condition or problem not lited above?</span><span class="yn">YES/NO</span></div>
    <div class="answer-field" style="height:20px;margin-top:4px"></div>
  </div>
  <div class="abs question" style="top:819px;border-top:none">
    <div class="question-row"><span>Have you had surgery or been to hospital in the last 5 years? (If YES,Please give details)</span><span class="yn">YES/NO</span></div>
    <div class="answer-field" style="height:20px;margin-top:4px"></div>
  </div>
  <div class="abs question" style="top:866px;border-top:none">
    <div class="question-row"><span>For Women:Are you pregnant? (If YES, How many months?)</span><span class="yn">YES/NO</span></div>
    <div class="answer-field" style="height:20px;margin-top:4px"></div>
  </div>
  <div class="abs question" style="top:912px;border-top:none">
    <div class="question-row"><span>Do you currently or have you ever smoked?</span><span class="yn">YES/NO</span></div>
    <div class="answer-field" style="height:20px;margin-top:4px"></div>
  </div>

  <p class="abs declaration">The information that I have provided is to the best of my knowledge true and I understand that is my responsibility to inform of any changes in my medical status.</p>
  <div class="abs signature">
    <span>Patient/Parent/Person Responsible signature:</span><span class="sign-line" style="width:132px"></span>
    <span style="margin-left:36px">Date:</span><span class="sign-line" style="width:110px"></span>
  </div>

  <svg class="footer-band" viewBox="0 0 781 80" preserveAspectRatio="none" aria-hidden="true">
    <defs>
      <linearGradient id="footGrad" x1="0" y1="0" x2="1" y2="0">
        <stop offset="0" stop-color="#0255a3"/>
        <stop offset="0.5" stop-color="#0692cd"/>
        <stop offset="1" stop-color="#0255a3"/>
      </linearGradient>
    </defs>
    <path d="M0 12C150 0 300 22 430 14C560 6 680 2 781 12V80H0Z" fill="#34a6d7" opacity="0.5"/>
    <path d="M0 18C150 6 300 28 430 20C560 12 680 8 781 18V80H0Z" fill="url(#footGrad)"/>
  </svg>
  <div class="abs footer-url">www.corvinadental.net</div>

</div>
</body>
</html>
```